International Travel Technology R&D business needs a wordpress website

We are a start up team of initially 2 individuals but plan to grow our team quickly, we have deep experience in travel technology. Our goal is to provide next generation technology research and development on behalf of our clients who are leading players in the travel technology industry. Attached our logos.

Target Market(s)

Travel Technology companies

Industry/Entity Type

Travel Industry

Coding

Coded - Design and coding required

Font styles to use
Sans Serif

Requirements
Must have
• Make use of our logo and colour scheme in the attached. Has to have a sense of adventure/ stepping into the unknown but equally must convey a sense of professionalism , we are a safe pair of hands. Sample themes are in the attachment .
Nice to have
• We have identified a theme on skinharbor which we feel would be inspirational. We hahe attached them to help in the design as inspiration.
Should not have
• images of airplanes , hotels etc, we want to project a future image.

```html
<!DOCTYPE html>
<html lang="en">
<head>
<meta charset="utf-8">
<title>Wayfront Labs</title>
<link href="https://fonts.googleapis.com/css2?family=Roboto:wght@300;400;500;700&family=Covered+By+Your+Grace&display=swap" rel="stylesheet">
<style>
:root{
  --sky:#5ab8f5;
  --sky-deep:#3ea6ec;
  --sky-light:#8fd0fa;
  --green:#56b61a;
  --ink:#222831;
  --text:#555a60;
  --muted:#8a8f95;
  --paper:#f4f6f8;
  --white:#ffffff;
  --navy:#1f3557;
}
*{box-sizing:border-box;margin:0;padding:0}
html,body{width:1200px;height:2264px;overflow:hidden}
body{position:relative;font-family:"Roboto",Arial,sans-serif;color:var(--text);background:var(--white)}
.abs{position:absolute}

/* top bar */
.topbar{left:0;top:0;width:1200px;height:35px;background:var(--white)}
.topbar .item{position:absolute;top:9px;font-size:14px;color:var(--green);display:flex;align-items:center;gap:6px}
.pill{position:absolute;top:7px;height:21px;border-radius:4px;color:#fff;font-size:14px;font-weight:500;display:flex;align-items:center;justify-content:center}
.pill.login{left:913px;width:60px;background:var(--green)}
.pill.jobs{left:997px;width:41px;background:var(--sky-deep)}
.dot-icon{position:absolute;top:12px;width:11px;height:11px;border-radius:50%;background:var(--green)}

/* nav */
.navband{left:0;top:35px;width:1200px;height:66px;background:var(--sky)}
.nav a{position:absolute;top:21px;color:#fff;font-size:17px;font-weight:500;text-decoration:none;letter-spacing:.2px}
.brand{left:54px;top:0;width:281px;height:113px;background:var(--white);border-radius:0 0 10px 10px;box-shadow:0 3px 10px rgba(0,0,0,.18);display:flex;align-items:center;justify-content:center;gap:12px}
.brand .mark{width:22px;height:22px;border-radius:50%;background:var(--sky-deep)}
.brand .name{font-size:30px;font-weight:700;color:var(--navy);letter-spacing:1px}

/* hero */
.hero{left:0;top:101px;width:1200px;height:489px;background:linear-gradient(160deg,#4a4f57 0%,#2e333a 45%,#5a5040 75%,#2a2d33 100%)}
.hero-title{left:0;top:158px;width:1200px;text-align:center;font-family:"Covered By Your Grace",cursive;color:#fff;font-size:86px;line-height:90px}
.hero-sub{left:0;top:345px;width:1200px;text-align:center;color:#fff;font-size:21px;font-weight:500;line-height:29px}
.btn{position:absolute;top:427px;height:32px;border-radius:3px;font-size:10px;font-weight:700;color:#fff;display:flex;align-items:center;justify-content:center;letter-spacing:.3px}
.btn.solid{left:495px;width:71px;background:var(--green)}
.btn.ghost{left:616px;width:95px;border:1.5px solid var(--green)}
.dots{left:567px;top:557px;display:flex;gap:8px}
.dots span{width:9px;height:9px;border-radius:50%;border:1.5px solid #fff}
.dots span.on{background:#fff}

/* about */
.about{left:0;top:590px;width:1200px;height:361px;background:var(--paper)}
.section-title{position:absolute;left:0;width:1200px;text-align:center;font-size:23px;font-weight:500;color:var(--ink)}
.rule{position:absolute;left:40px;width:1120px;border-top:2px dotted var(--green)}
.feature{position:absolute;top:104px;width:340px;text-align:center}
.feature .icon{width:76px;height:80px;margin:0 auto;border-radius:4px;background:linear-gradient(180deg,#7ccbfb,#3ea6ec);display:flex;align-items:center;justify-content:center}
.feature h3{margin-top:15px;font-size:19px;font-weight:500;color:var(--ink)}
.feature p{margin-top:14px;font-size:13px;line-height:20px;font-weight:300;color:var(--text)}

/* parallax band */
.parallax{left:0;top:951px;width:1200px;height:274px;background:linear-gradient(180deg,#6f86aa 0%,#3d5174 45%,#1e2a40 100%);box-shadow:0 0 18px rgba(90,184,245,.8)}
.parallax .note{position:absolute;left:4px;bottom:4px;font-family:"Covered By Your Grace",cursive;color:#fff;font-size:20px}

/* services */
.illustration{left:53px;top:1336px;width:532px;height:404px;background:linear-gradient(180deg,#eaf6fe 0%,#cfeafd 55%,#a9dbfb 100%)}
.accordion{left:614px;top:1352px;width:530px}
.acc-item{position:absolute;left:0;display:flex;align-items:center;gap:12px;font-size:17px;color:var(--ink);font-weight:400;white-space:nowrap}
.chev{width:26px;height:26px;border-radius:3px;background:#eef3f7;display:flex;align-items:center;justify-content:center}
.acc-item.open{color:var(--sky-deep)}
.acc-item.open .chev{background:var(--sky-deep)}
.acc-body{position:absolute;left:38px;top:36px;width:490px;font-size:13.5px;line-height:20px;font-weight:300;color:var(--text)}

/* skyline + footer */
.skyline{left:0;top:1750px;width:1200px;height:68px;background:linear-gradient(180deg,rgba(90,184,245,0) 0%,rgba(90,184,245,.35) 60%,var(--sky) 100%)}
.footer{left:0;top:1818px;width:1200px;height:446px;background:radial-gradient(ellipse at 50% 70%,#79c8fa 0%,var(--sky) 55%,#4cadef 100%)}
.col{position:absolute;top:58px;width:255px;color:#fff}
.col h4{font-size:19px;font-weight:500;margin-bottom:16px}
.col p{font-size:13px;line-height:19px;margin-bottom:14px}
.col b{font-weight:700}
.field{position:absolute;left:0;width:251px;background:#fff;border-radius:4px;font-size:13px;color:var(--muted);padding:8px 12px}
.send{position:absolute;left:0;top:214px;width:134px;height:32px;background:var(--green);color:#fff;font-size:13px;font-weight:700;border-radius:3px;display:flex;align-items:center;justify-content:center}
.map{position:absolute;left:0;top:34px;width:254px;height:214px;background:linear-gradient(135deg,#e7eef3 0%,#d7e4ec 50%,#a9d0ea 100%)}
.socials{display:flex;gap:12px;margin-top:6px}
.socials span{width:13px;height:13px;border-radius:50%;background:#fff}
.foot-rule{position:absolute;left:53px;top:375px;width:1094px;border-top:1px solid rgba(255,255,255,.55)}
.copyright{position:absolute;left:0;top:404px;width:1200px;text-align:center;color:#fff;font-size:13px;font-weight:500}
</style>
</head>
<body>

<header class="abs topbar">
  <div class="item" style="left:575px">
    <svg width="12" height="12" viewBox="0 0 24 24"><path fill="#56b61a" d="M6.6 10.8a15.1 15.1 0 0 0 6.6 6.6l2.2-2.2c.3-.3.7-.4 1-.2 1.1.4 2.3.6 3.6.6.6 0 1 .4 1 1V20c0 .6-.4 1-1 1A17 17 0 0 1 3 4c0-.6.4-1 1-1h3.5c.6 0 1 .4 1 1 0 1.3.2 2.5.6 3.6.1.3 0 .7-.2 1z"/></svg>
    +1 800 555 0142
  </div>
  <div class="item" style="left:727px">
    <svg width="13" height="10" viewBox="0 0 26 20"><rect width="26" height="20" rx="2" fill="#56b61a"/><path d="M1 2l12 9 12-9" stroke="#fff" stroke-width="2" fill="none"/></svg>
    hello@wayfrontlabs.net
  </div>
  <div class="pill login">Login</div>
  <div class="pill jobs">Jobs</div>
  <span class="dot-icon" style="left:1054px"></span>
  <span class="dot-icon" style="left:1089px"></span>
  <svg class="abs" style="left:1132px;top:11px" width="13" height="13" viewBox="0 0 20 20"><circle cx="8" cy="8" r="6" stroke="#56b61a" stroke-width="3" fill="none"/><path d="M12.5 12.5l6 6" stroke="#56b61a" stroke-width="3"/></svg>
</header>

<nav class="abs navband nav">
  <a style="left:548px">HOME</a>
  <a style="left:634px">COMPANY</a>
  <a style="left:750px">SERVICES</a>
  <a style="left:866px">SOLUTIONS</a>
  <a style="left:994px">BLOG</a>
  <a style="left:1074px">CONTACT</a>
</nav>

<div class="abs brand">
  <span class="mark"></span>
  <span class="name">WAYFRONT LABS</span>
</div>

<section class="abs hero" role="img" aria-label="Photo of a busy open-plan research office with desks and monitors">
  <h1 class="abs hero-title" style="top:57px">Welcome to<br>Wayfront Labs</h1>
  <p class="abs hero-sub" style="top:244px">Your trusted market research provider, dedicated to the<br>provision of meaningful and actionable insights</p>
  <div class="btn solid">ABOUT US</div>
  <div class="btn ghost">GO ON SURFING</div>
  <div class="abs dots" style="top:456px"><span class="on"></span><span></span><span></span><span></span></div>
</section>

<section class="abs about">
  <h2 class="section-title" style="top:22px">Partners &amp; Travel Technology Companies</h2>
  <div class="rule" style="top:61px"></div>

  <div class="feature" style="left:54px">
    <div class="icon">
      <svg width="40" height="40" viewBox="0 0 40 40" fill="none" stroke="#fff" stroke-width="2.2" stroke-linejoin="round"><rect x="5" y="17" width="7" height="17"/><path d="M12 19l7-11c2-2 4 0 4 2l-2 7h10c2 0 3 2 2.5 4l-3 10c-.5 2-2 3-4 3H12"/></svg>
    </div>
    <h3>Who we are</h3>
    <p>The quality perception of the product, what clients would like to change, what price can they afford, where is this product wanted the most, what causes dissatisfaction in a product (i.e. price, quality,design)</p>
  </div>

  <div class="feature" style="left:430px">
    <div class="icon">
      <svg width="40" height="44" viewBox="0 0 40 44" fill="none" stroke="#fff" stroke-width="2"><path d="M20 4c6 5 7 14 4 24h-8c-3-10-2-19 4-24z"/><circle cx="20" cy="16" r="3"/><path d="M16 28l-5 5 4 0M24 28l5 5-4 0M20 31v8"/></svg>
    </div>
    <h3>Our Mission</h3>
    <p>Wayfront Labs is a team of research professionals that work toward delivering research services while upholding the highest standards of design, analysis and reporting. Our mission is to help set the industry in consulting services</p>
  </div>

  <div class="feature" style="left:805px">
    <div class="icon">
      <svg width="34" height="42" viewBox="0 0 34 42" fill="none" stroke="#fff" stroke-width="2"><path d="M4 3h18l8 8v28H4z"/><path d="M22 3v8h8M10 18h14M10 24h14M10 30h14"/></svg>
    </div>
    <h3>Our Vision</h3>
    <p>Our vision is to be a long-term preferred partner to our clients in the field of market research and business consulting. We are relentlessly focused on delivering exceptional value in provision of strategy, research and analysis</p>
  </div>
</section>

<section class="abs parallax" role="img" aria-label="Aerial photo of a dense city skyline at dusk">
  <span class="note">Parallax image move on mause scroll</span>
</section>

<h2 class="section-title" style="top:1252px">What We Do</h2>
<div class="rule" style="top:1293px;left:53px;width:1094px"></div>

<div class="abs illustration" role="img" aria-label="Flat blue illustration of three analysts at laptops in front of a city with chart dashboards"></div>

<div class="abs accordion">
  <div class="acc-item open" style="top:0">
    <span class="chev"><svg width="12" height="8" viewBox="0 0 12 8"><path d="M1 7l5-5 5 5" stroke="#fff" stroke-width="1.8" fill="none"/></svg></span>
    Opinion Polling
  </div>
  <p class="acc-body">Opinion polls are an integral part of political debates, the state of the economy, social trends and more. Simply put, we report what people think, along with what they do, because it is important. We generate original public opinion data and other information that is relevant, timely and accurate</p>
  <div class="acc-item" style="top:136px"><span class="chev"><svg width="12" height="8" viewBox="0 0 12 8"><path d="M1 1l5 5 5-5" stroke="#5ab8f5" stroke-width="1.8" fill="none"/></svg></span>Social and Economic Policy Analysis</div>
  <div class="acc-item" style="top:192px"><span class="chev"><svg width="12" height="8" viewBox="0 0 12 8"><path d="M1 1l5 5 5-5" stroke="#5ab8f5" stroke-width="1.8" fill="none"/></svg></span>Project Evaluation and Impact Assessment</div>
  <div class="acc-item" style="top:249px"><span class="chev"><svg width="12" height="8" viewBox="0 0 12 8"><path d="M1 1l5 5 5-5" stroke="#5ab8f5" stroke-width="1.8" fill="none"/></svg></span>Feasibility Studies</div>
  <div class="acc-item" style="top:305px"><span class="chev"><svg width="12" height="8" viewBox="0 0 12 8"><path d="M1 1l5 5 5-5" stroke="#5ab8f5" stroke-width="1.8" fill="none"/></svg></span>New Product Development</div>
  <div class="acc-item" style="top:361px"><span class="chev"><svg width="12" height="8" viewBox="0 0 12 8"><path d="M1 1l5 5 5-5" stroke="#5ab8f5" stroke-width="1.8" fill="none"/></svg></span>Market Size and Segmentation Studies</div>
</div>

<div class="abs skyline" role="img" aria-label="Blue silhouette of a city skyline and airport along the footer edge"></div>

<footer class="abs footer">
  <div class="col" style="left:53px">
    <h4>Contact Us</h4>
    <p>Maecenas etos sit amet, consectetur adipiscing elit. Terminal volutpat rutrum metro amet sollicitudin interdum.</p>
    <p><b>Phone:</b> +1 (800) 555 0187</p>
    <p><b>Office:</b> 418 Harbor Lane, Lakeview</p>
    <p><b>Email:</b> info@wayfrontlabs.net</p>
    <div class="socials"><span></span><span></span><span></span><span></span><span></span></div>
  </div>

  <div class="col" style="left:334px">
    <h4>Feel Free to Mail</h4>
    <div class="field" style="top:36px;height:32px">Name *</div>
    <div class="field" style="top:87px;height:32px">Email *</div>
    <div class="field" style="top:138px;height:56px">Write Your Message Here...</div>
    <div class="send">SEND MESSAGE</div>
  </div>

  <div class="col" style="left:614px">
    <h4>Headquarters</h4>
    <div class="map" role="img" aria-label="Street map showing the office location"></div>
  </div>

  <div class="col" style="left:895px">
    <h4>Last Review</h4>
    <p>Enim congue blandit. Lorem ipsum dolor sit amet, consectetur adipiscing elit. Quisque consectetur interdum finibus. Vestibulum ante ipsum primis in faucibus orci. luctus et ultrices posuere.</p>
    <p>Cubilia cras blandit finibus ipsum, id porttitor arcu volutpat a. Integer iaculis erat nec justo malesuada faucibus vel tempus sapien. Vivamus aliquam euismod tristique.</p>
  </div>

  <div class="foot-rule"></div>
  <p class="copyright">Copyright 2020. All Rights Reserved by Wayfront Labs</p>
</footer>

</body>
</html>
```